Holistic Psychology clinic flyer-

We need a 3 fold flyer that is both professional and zen looking with holistic elements- bilingual on both sides.
I am looking for a design that conveys the sense of confidence, yet relaxing to the eye and makes people want to pick it up and read it!
We are all about balance (yin, yang) and bringing equilibrium to a person in their quest to get better.

Target Market(s)

families adults, teens children experiencing mental health issues

Industry/Entity Type

Psychologist

Font styles to use
Serif

Colors
fbf289
cee9f5
0455a3

Requirements
Must have
• my logo (spiral) ; French one side; English on the other. Text is provided; Some color but clean, zen elements
• Easy to read text
Nice to have
• nature elements, bamboo? trees etc. sunrise or sunset?
• The sunset back ground provided in the picture is not necessary
• families?
Should not have
• too many distracting elements; not too many colors. colors must be subtle and must flow together

```html
<!DOCTYPE html>
<html lang="en">
<head>
<meta charset="utf-8">
<title>Clinique Sérénia – Trifold</title>
<link rel="stylesheet" href="https://fonts.googleapis.com/css2?family=Merriweather:ital,wght@0,400;0,700;0,900;1,900&family=Source+Serif+4:wght@400;600&display=swap">
<style>
  :root {
    --sky-deep: #1f5fb3;
    --sky-mid: #6f92c8;
    --haze: #c9c7c0;
    --sun-gold: #f8cf4e;
    --sun-orange: #f6b530;
    --pale-yellow: #fbf289;
    --water-light: #cee9f5;
    --water-deep: #0455a3;
    --ink: #1e1f5c;
    --white: #ffffff;
  }
  * { margin: 0; padding: 0; box-sizing: border-box; }
  html, body { width: 1200px; height: 848px; overflow: hidden; background: #fff; }
  .trifold {
    position: relative; width: 1200px; height: 848px; overflow: hidden;
    font-family: "Source Serif 4", Georgia, serif; color: var(--ink);
  }
  .backdrop {
    position: absolute; inset: 0;
    background: linear-gradient(to bottom,
      var(--sky-deep) 0%, var(--sky-mid) 14%, var(--haze) 26%,
      #f4dc86 36%, var(--sun-gold) 50%, var(--sun-orange) 63.9%,
      #fbe27c 64%, var(--pale-yellow) 72%, var(--water-light) 78%,
      #6aa2d6 86%, var(--water-deep) 100%);
  }
  .panel { position: absolute; top: 0; height: 848px; }
  .panel--services { left: 36px; width: 328px; }
  .panel--welcome { left: 435px; width: 328px; }
  .panel--cover { left: 800px; width: 400px; }

  .panel-title {
    position: absolute; top: 48px; left: 0;
    font-family: "Merriweather", Georgia, serif; font-weight: 700;
    font-size: 22.5px; color: var(--white); white-space: nowrap;
  }

  .service { position: absolute; left: 0; width: 328px; }
  .service h3 {
    font-family: "Merriweather", Georgia, serif; font-weight: 700;
    font-size: 13.5px; line-height: 17.2px;
  }
  .body-text {
    font-size: 14px; line-height: 17.2px; text-align: justify;
  }
  .service--clinical { top: 99px; }
  .service--integrative { top: 202px; }
  .service--coaching { top: 305px; }
  .service--sports { top: 408px; }
  .service--assess { top: 510px; }
  .service--mindful { top: 647px; }

  .welcome-para { position: absolute; left: 0; width: 328px; }
  .welcome-para--one { top: 99px; }
  .welcome-para--two { top: 185px; }
  .welcome-para--three { top: 322px; }
  .mantra {
    position: absolute; top: 394px; left: 0; width: 328px; text-align: center;
    font-size: 18px; line-height: 22px;
  }
  .founder { position: absolute; top: 481px; left: 0; width: 328px; }
  .cta {
    position: absolute; top: 659px; left: 0; width: 328px; text-align: center;
    font-size: 18px; line-height: 22px;
  }
  .cta-phone {
    position: absolute; top: 728px; left: 0; width: 328px; text-align: center;
    font-family: "Merriweather", Georgia, serif; font-weight: 900;
    font-size: 24px; letter-spacing: 1px; color: var(--white);
  }
  .cta-email {
    position: absolute; top: 766px; left: 0; width: 328px; text-align: center;
    font-size: 20px; color: var(--white);
  }

  .brand {
    position: absolute; top: 88px; left: 40px;
    display: flex; align-items: center; gap: 12px;
    font-family: "Source Serif 4", Georgia, serif; font-weight: 400;
    font-size: 50px; color: var(--ink);
  }
  .brand-dot { width: 26px; height: 26px; border-radius: 50%; background: var(--pale-yellow); }
  .clinic-name {
    position: absolute; top: 228px; left: 38px;
    font-family: "Merriweather", Georgia, serif; font-weight: 900;
    font-size: 32px; color: var(--ink); white-space: nowrap;
  }
  .tagline {
    position: absolute; top: 288px; left: 40px;
    font-family: "Merriweather", Georgia, serif; font-weight: 900; font-style: italic;
    font-size: 21px; line-height: 27px; color: var(--ink);
  }
  .audience {
    position: absolute; top: 545px; left: 42px; list-style: none;
    font-family: "Merriweather", Georgia, serif; font-weight: 900; font-style: italic;
    font-size: 17.5px; line-height: 27px;
  }
  .audience li { display: flex; align-items: center; gap: 16px; }
  .audience li::before {
    content: ""; width: 10px; height: 10px; border-radius: 50%; background: var(--ink);
  }
  .contact {
    position: absolute; top: 681px; left: 0; width: 400px; text-align: center;
    font-style: normal; font-size: 15.5px; line-height: 20px;
  }
  .contact .tel { font-size: 18.5px; line-height: 24px; }
  .web-band {
    position: absolute; top: 798px; left: 0; width: 400px; height: 27px;
    background: var(--pale-yellow); text-align: center; white-space: nowrap;
    font-size: 16px; line-height: 27px; letter-spacing: 6px; color: var(--ink);
  }
</style>
</head>
<body>
<main class="trifold">
  <div class="backdrop" role="img" aria-label="Sunset over calm water: blue sky fading to a golden sun and gulls above a blue sea"></div>

  <section class="panel panel--services">
    <h2 class="panel-title">Our Professional Services</h2>
    <article class="service service--clinical">
      <h3>Clinical Psychology</h3>
      <p class="body-text">Psychologists are people specialists. Learn how to better understand both yourself and those in your life. Release some of the emotional and relational distress that drains you. It’s time for change!</p>
    </article>
    <article class="service service--integrative">
      <h3>Integrative Psychotherapy</h3>
      <p class="body-text">We distill the very best approaches in psychology to help you free your mind, balance your body and heal your spirit. We specialize in helping you understand and harmonize the mind-body connection.</p>
    </article>
    <article class="service service--coaching">
      <h3>Life Coaching</h3>
      <p class="body-text">Life’s challenges are opportunities for your growth. Our life coaches are skilled, caring and passionate about supporting you. Come in, it’s time to discover your potential!</p>
    </article>
    <article class="service service--sports">
      <h3>Sports Psychology</h3>
      <p class="body-text">There are many different psychological benefits of sports. Our sports psychologists can work with you to release your mental blocks, improve your performance and ensure success! Dare to aim high!</p>
    </article>
    <article class="service service--assess">
      <h3>Psycho-Educational Assessments</h3>
      <p class="body-text">With the aid of psychometric tests, we can help you to figure out how your mind or that of your child works. We will highlight strengths and give recommendations to remedy any weaknesses. A detailed report and an academic intervention plan is customized for individuals aged 4-64!</p>
    </article>
    <article class="service service--mindful">
      <h3>Mindfulness Meditation Classes</h3>
      <p class="body-text">Meditation is much more than a relaxation technique. Mindfulness will bring you a heightened awareness and improved quality of life. These classes are offered weekly and will be useful to you to learn how to meditate and integrate it into your daily life. Find your inner peace!</p>
    </article>
  </section>

  <section class="panel panel--welcome">
    <h2 class="panel-title">Welcome to Sérénia !</h2>
    <p class="body-text welcome-para welcome-para--one">We present you with a whole new way of achieving wellness in your life. We offer a variety of clinical and educational services in a professional and peaceful environment. We use an integrative approach.</p>
    <p class="body-text welcome-para welcome-para--two">We are delighted to present you with several effective and scientific approaches that can help you. We offer a variety of clinical and educational services in a professional and peaceful environment. We are committed to supporting you in reaching your potential and feeling better by adhering to an integrative mind-body approach.</p>
    <p class="body-text welcome-para welcome-para--three">We are passionate about supporting you in reaching your potential and feeling well. It’s time to start thinking of you...</p>
    <p class="mantra">CALM YOUR MIND,<br>RELAX YOUR BODY,<br>NOURISH YOUR SPIRIT.</p>
    <p class="body-text founder">Laurent Dufresne, BSc, MA. is the founder and director of Sérénia. As a clinical psychologist, author and motivational speaker with 26 years of experience, Laurent is a pioneer in holistic psychology, an integrative approach that promotes healing and wellness. He and his staff are skilled in using cutting edge mind-body-spirit tools to help you with a variety of health, relational, educational and parenting issues. We look forward to supporting you and your family</p>
    <p class="cta">Contact us today for a<br>free phone consultation</p>
    <p class="cta-phone">514-555-0147</p>
    <p class="cta-email">info@serenia-clinic.ca</p>
  </section>

  <section class="panel panel--cover">
    <div class="brand"><span class="brand-dot"></span>Sérénia</div>
    <h1 class="clinic-name">Clinique Sérénia</h1>
    <p class="tagline">Psychologists<br>and Educational<br>Professionals<br>with an Integrative<br>Approach</p>
    <ul class="audience">
      <li>Children</li>
      <li>Teens</li>
      <li>Adults</li>
      <li>Couples</li>
    </ul>
    <address class="contact">
      4310 Rivière Blvd , Beaconsfield,<br>Québec H9W 2K5<br>
      <span class="tel">Tel: (514) 555-0147</span><br>
      info@serenia-clinic.ca<br>
      www.facebook.com/SereniaClinic
    </address>
    <div class="web-band">www.serenia-clinic.ca</div>
  </section>
</main>
</body>
</html>
```